Lakeshore Claims Collective Business card

We need to get business card Design for our Company we are Public Adjusters in Chicago Illinois - i like to see good combination and elements from my Company Logo. as well To be an two side design
Updates

Target Market(s)

Home /Business owner Property Managers

Industry/Entity Type

Business

Contact Information for Business Card

to show the Element of our logo i will Like 3D

Font styles to use
Sans Serif

Requirements
Must have
• Logo and Element of the Logo in 3D
Nice to have
• Logo That we Provide 3D Same Colors or open for suggestions
Should not have
• unleare view -

```html
<!DOCTYPE html>
<html lang="en">
<head>
<meta charset="utf-8">
<title>Lakeshore Claims Collective – Business Card</title>
<link href="https://fonts.googleapis.com/css2?family=PT+Sans:wght@400;700&display=swap" rel="stylesheet">
<style>
  :root {
    --stage: #141414;
    --card-white: #ffffff;
    --navy: #11128a;
    --navy-deep: #07087a;
    --blue-glow: #1f2ad6;
    --ink: #3d3d3d;
    --rule: #9fc3e0;
    --white: #ffffff;
  }
  * { box-sizing: border-box; margin: 0; padding: 0; }
  html, body { width: 1200px; height: 900px; overflow: hidden; }
  body {
    background: var(--stage);
    font-family: "PT Sans", sans-serif;
    position: relative;
  }
  .card {
    position: absolute;
    top: 306px;
    width: 440px;
    height: 271px;
    border-radius: 12px;
    box-shadow: 0 6px 18px rgba(0,0,0,0.5);
  }
  .card--front { left: 149px; background: var(--card-white); }
  .card--back {
    left: 608px;
    background: radial-gradient(ellipse at 50% 40%, var(--blue-glow) 0%, var(--navy-deep) 55%, #050560 100%);
  }

  .brand { position: absolute; left: 0; right: 0; text-align: center; }
  .brand__dot { display: block; margin: 0 auto; border-radius: 50%; }
  .brand__name { font-weight: 700; display: block; }

  .card--front .brand { top: 22px; }
  .card--front .brand__dot { width: 58px; height: 58px; background: var(--navy); }
  .card--front .brand__name { color: var(--navy); font-size: 15px; margin-top: 44px; }

  .card--back .brand { top: 50px; }
  .card--back .brand__dot { width: 86px; height: 86px; background: var(--white); }
  .card--back .brand__name { color: var(--white); font-size: 19px; margin-top: 70px; }

  .address {
    position: absolute; left: 27px; top: 150px;
    color: var(--ink); font-size: 12.5px; line-height: 16px;
  }
  .person { position: absolute; right: 29px; top: 169px; text-align: right; }
  .person__name { color: var(--navy); font-size: 16px; font-weight: 700; }
  .person__role { color: var(--ink); font-size: 12px; margin-top: 4px; }
  .rule {
    position: absolute; left: 27px; right: 29px; top: 190px;
    border-top: 1px solid var(--rule);
  }
  .contacts {
    position: absolute; left: 27px; top: 201px; list-style: none;
    color: var(--ink); font-size: 12.5px; line-height: 16px;
  }
  .contacts li { display: flex; align-items: center; gap: 7px; }
  .contacts svg { width: 9px; height: 9px; fill: var(--navy); }
</style>
</head>
<body>
  <section class="card card--front">
    <div class="brand">
      <span class="brand__dot"></span>
      <span class="brand__name">Lakeshore Claims Collective</span>
    </div>
    <p class="address">48 Lakeview Avenue<br>Chicago, IL 60601.</p>
    <div class="person">
      <p class="person__name">Morgan Hale</p>
      <p class="person__role">Managing Director</p>
    </div>
    <div class="rule"></div>
    <ul class="contacts">
      <li><svg viewBox="0 0 10 10"><path d="M2 0.5 L3.8 2.6 L2.9 3.6 Q4 5.8 6.4 7.1 L7.4 6.2 L9.5 8 L8.3 9.5 Q1.5 8 0.5 1.7 Z"/></svg>044-987 654 321</li>
      <li><svg viewBox="0 0 10 10"><path d="M0.5 2 H9.5 V8 H0.5 Z"/><path d="M1 2.6 L5 5.6 L9 2.6" fill="none" stroke="#fff" stroke-width="0.8"/></svg>hello@lakeshoreclaims.com</li>
      <li><svg viewBox="0 0 10 10"><circle cx="5" cy="5" r="4.5"/><path d="M0.5 5 H9.5 M5 0.5 Q2.5 5 5 9.5 M5 0.5 Q7.5 5 5 9.5" fill="none" stroke="#fff" stroke-width="0.6"/></svg>www.lakeshoreclaims.com</li>
    </ul>
  </section>

  <section class="card card--back">
    <div class="brand">
      <span class="brand__dot"></span>
      <span class="brand__name">Lakeshore Claims Collective</span>
    </div>
  </section>
</body>
</html>
```